Bright Harbor Painters Banner

Create a banner that displays and reinforces Bright Harbor Painters’ brand identity while promoting our interior painting services. The banner will be displayed at indoor venues through the winter. The design should be clean, professional, and visually recognizable to both new and returning customers. See attached design brief & logo source files.

```html
<!DOCTYPE html>
<html lang="en">
<head>
<meta charset="utf-8">
<title>Bright Harbor Painters Banner</title>
<link rel="stylesheet" href="https://fonts.googleapis.com/css2?family=Anton&family=Oswald:wght@700&family=Poppins:ital,wght@1,800&family=Montserrat:wght@700;800&family=Open+Sans:ital,wght@0,500;1,800&family=Roboto+Condensed:wght@400;700&display=swap">
<style>
  :root {
    --brand-green: #76984f;
    --brand-charcoal: #4a4a48;
    --brand-white: #fafafa;
    --page-bg: #e6e9ec;
  }
  * { box-sizing: border-box; margin: 0; padding: 0; }
  html, body { width: 1200px; height: 840px; overflow: hidden; }
  body { background: var(--page-bg); position: relative; }

  .banner {
    position: absolute; left: 40px; top: 202px;
    width: 1120px; height: 436px;
    background: var(--brand-green);
    overflow: hidden;
  }
  .banner__curve { position: absolute; left: 0; top: 0; width: 1120px; height: 350px; }

  .headline { position: absolute; left: 52px; top: 26px; }
  .headline__main {
    font-family: "Anton", sans-serif; font-size: 122px; line-height: 1;
    color: var(--brand-white); letter-spacing: 1px;
  }
  .headline__sub {
    font-family: "Oswald", sans-serif; font-weight: 700; font-size: 56px; line-height: 1;
    color: var(--brand-charcoal); margin-top: 4px; letter-spacing: 0.5px;
  }
  .headline__rule {
    width: 360px; height: 3px; background: var(--brand-charcoal); margin-top: 14px;
  }

  .service-list {
    position: absolute; left: 52px; top: 236px; width: 540px;
    display: flex; flex-wrap: wrap; gap: 6px 16px; list-style: none;
  }
  .service-list__item {
    display: flex; align-items: center; gap: 4px;
    font-family: "Poppins", sans-serif; font-style: italic; font-weight: 800;
    font-size: 30px; line-height: 1.3; color: var(--brand-white);
  }
  .service-list__tick { width: 28px; height: 28px; flex: none; }

  .brand {
    position: absolute; left: 700px; top: 40px; width: 400px;
    display: flex; flex-direction: column; align-items: center;
  }
  .brand__dot { width: 74px; height: 74px; border-radius: 50%; background: var(--brand-green); }
  .brand__name {
    margin-top: 18px; text-align: center;
    font-family: "Montserrat", sans-serif; font-weight: 800; font-size: 38px; line-height: 1.1;
    color: var(--brand-charcoal); letter-spacing: 1px;
  }
  .brand__rule { width: 400px; height: 1.5px; background: var(--brand-charcoal); margin-top: 14px; }
  .brand__tagline {
    margin-top: 10px;
    font-family: "Montserrat", sans-serif; font-weight: 700; font-size: 17px;
    color: var(--brand-green);
  }

  .footer-band {
    position: absolute; left: 0; top: 350px; width: 1120px; height: 86px;
    background: var(--brand-charcoal);
  }
  .cta-pill {
    position: absolute; left: 0; top: 20px; width: 476px; height: 46px;
    background: var(--brand-white); border-radius: 0 23px 23px 0;
    display: flex; align-items: center; justify-content: flex-end; padding-right: 18px;
    font-family: "Open Sans", sans-serif; font-weight: 500; font-size: 27px;
    color: var(--brand-charcoal); letter-spacing: 0.5px;
  }
  .cta-pill__emph { font-style: italic; font-weight: 800; margin: 0 8px; }
  .web-address {
    position: absolute; left: 520px; top: 6px;
    display: flex; align-items: center; gap: 10px;
    font-family: "Roboto Condensed", sans-serif; font-size: 60px; line-height: 1;
    color: var(--brand-white);
  }
  .web-address__icon { width: 46px; height: 46px; }
  .web-address__domain { font-weight: 700; }
</style>
</head>
<body>
  <section class="banner" aria-label="Bright Harbor Painters interior painting banner">
    <svg class="banner__curve" viewBox="0 0 1120 350" aria-hidden="true">
      <path d="M790 0 C690 40 604 150 600 350 L1120 350 L1120 0 Z" fill="var(--brand-charcoal)"/>
      <path d="M826 0 C724 52 642 160 640 350 L1120 350 L1120 0 Z" fill="var(--brand-white)"/>
    </svg>

    <div class="headline">
      <h1 class="headline__main">INTERIOR</h1>
      <h2 class="headline__sub">PAINTING SERVICES</h2>
      <div class="headline__rule"></div>
    </div>

    <ul class="service-list">
      <li class="service-list__item"><svg class="service-list__tick" viewBox="0 0 28 28"><rect x="2" y="6" width="20" height="20" rx="3" fill="none" stroke="var(--brand-white)" stroke-width="3"/><path d="M7 15 L12 21 L25 3" fill="none" stroke="var(--brand-white)" stroke-width="4" stroke-linecap="round" stroke-linejoin="round"/></svg>Walls</li>
      <li class="service-list__item"><svg class="service-list__tick" viewBox="0 0 28 28"><rect x="2" y="6" width="20" height="20" rx="3" fill="none" stroke="var(--brand-white)" stroke-width="3"/><path d="M7 15 L12 21 L25 3" fill="none" stroke="var(--brand-white)" stroke-width="4" stroke-linecap="round" stroke-linejoin="round"/></svg>Ceilings</li>
      <li class="service-list__item"><svg class="service-list__tick" viewBox="0 0 28 28"><rect x="2" y="6" width="20" height="20" rx="3" fill="none" stroke="var(--brand-white)" stroke-width="3"/><path d="M7 15 L12 21 L25 3" fill="none" stroke="var(--brand-white)" stroke-width="4" stroke-linecap="round" stroke-linejoin="round"/></svg>Trim</li>
      <li class="service-list__item"><svg class="service-list__tick" viewBox="0 0 28 28"><rect x="2" y="6" width="20" height="20" rx="3" fill="none" stroke="var(--brand-white)" stroke-width="3"/><path d="M7 15 L12 21 L25 3" fill="none" stroke="var(--brand-white)" stroke-width="4" stroke-linecap="round" stroke-linejoin="round"/></svg>Cabinets</li>
      <li class="service-list__item"><svg class="service-list__tick" viewBox="0 0 28 28"><rect x="2" y="6" width="20" height="20" rx="3" fill="none" stroke="var(--brand-white)" stroke-width="3"/><path d="M7 15 L12 21 L25 3" fill="none" stroke="var(--brand-white)" stroke-width="4" stroke-linecap="round" stroke-linejoin="round"/></svg>Drywall Repair</li>
    </ul>

    <div class="brand">
      <div class="brand__dot" aria-hidden="true"></div>
      <p class="brand__name">BRIGHT HARBOR<br>PAINTERS</p>
      <div class="brand__rule"></div>
      <p class="brand__tagline">Trusted Local Professionals Since 2005</p>
    </div>

    <div class="footer-band">
      <p class="cta-pill">BOOK YOUR<span class="cta-pill__emph">FREE</span>ESTIMATE</p>
      <p class="web-address">
        <svg class="web-address__icon" viewBox="0 0 46 46" aria-hidden="true">
          <circle cx="23" cy="23" r="21" fill="var(--brand-green)"/>
          <circle cx="23" cy="23" r="21" fill="none" stroke="var(--brand-charcoal)" stroke-width="2"/>
          <ellipse cx="23" cy="23" rx="9" ry="21" fill="none" stroke="var(--brand-charcoal)" stroke-width="2"/>
          <line x1="2" y1="23" x2="44" y2="23" stroke="var(--brand-charcoal)" stroke-width="2"/>
        </svg>
        <span>www.<span class="web-address__domain">bhpainters</span>.com</span>
      </p>
    </div>
  </section>
</body>
</html>
```